Business Card Design for Occupational Medicine Start Up Company

We need to design a professional business card. We are a healthcare company providing occupational medicine services to blue collar industries. We are professional, efficient and high quality service providers.

Target Market(s)

Blue Collar Industry: Shipbuilding, Ports, Trucking Companies; The Executives and Safety Officers for these companies

Industry/Entity Type

Healthcare

Contact Information for Business Card

Logo, Name, Title, Email, Phone

Other font styles liked:
• Please match our Brand Guide

Requirements
Must have
• Our Company Colors and Logo

```html
<!DOCTYPE html>
<html lang="en">
<head>
<meta charset="UTF-8">
<title>CrewWell Clinics – Business Card</title>
<link href="https://fonts.googleapis.com/css2?family=Montserrat:wght@500;600&family=Arimo:wght@400;700&display=swap" rel="stylesheet">
<style>
  :root {
    --page-bg: #e4e4e6;
    --card-navy: #1f2580;
    --card-navy-deep: #161c6e;
    --edge-orange: #f4a533;
    --accent-blue: #2aa3e6;
    --text-white: #ffffff;
    --mark-blue: #3340b8;
  }
  * { margin: 0; padding: 0; box-sizing: border-box; }
  html, body {
    width: 1200px;
    height: 800px;
    overflow: hidden;
    background: var(--page-bg);
  }
  .canvas {
    width: 1200px;
    height: 800px;
    display: flex;
    align-items: center;
    justify-content: center;
    gap: 40px;
  }
  .card {
    position: relative;
    width: 540px;
    height: 309px;
    background: linear-gradient(135deg, var(--card-navy) 0%, var(--card-navy-deep) 100%);
    border-bottom: 3px solid var(--edge-orange);
    border-right: 2px solid var(--edge-orange);
    overflow: hidden;
  }

  /* Back: contact side */
  .card-back .corner-mark {
    position: absolute;
    top: 26px;
    right: 30px;
    display: flex;
    align-items: center;
    gap: 7px;
    font-family: "Montserrat", sans-serif;
    font-weight: 600;
    font-size: 11px;
    letter-spacing: 1px;
    color: var(--mark-blue);
  }
  .card-back .corner-mark .dot {
    width: 14px;
    height: 14px;
    border-radius: 50%;
    background: var(--mark-blue);
  }
  .identity {
    position: absolute;
    right: 290px;
    top: 118px;
    text-align: right;
    font-family: "Arimo", sans-serif;
  }
  .identity .person-name {
    font-weight: 700;
    font-size: 22px;
    color: var(--accent-blue);
    line-height: 1.1;
  }
  .identity .person-title {
    font-size: 14px;
    color: var(--text-white);
    margin-top: 2px;
  }
  .divider {
    position: absolute;
    left: 268px;
    top: 92px;
    width: 1px;
    height: 110px;
    background: rgba(255, 255, 255, 0.55);
  }
  .contact {
    position: absolute;
    left: 284px;
    top: 92px;
    font-family: "Arimo", sans-serif;
    font-size: 11.5px;
    line-height: 1.42;
    color: var(--text-white);
    list-style: none;
  }
  .contact li {
    display: flex;
    align-items: center;
    gap: 6px;
  }
  .contact li.address { padding-left: 16px; }
  .contact svg {
    width: 10px;
    height: 10px;
    flex: none;
  }

  /* Front: brand side */
  .card-front {
    display: flex;
    flex-direction: column;
    align-items: center;
    justify-content: center;
    gap: 10px;
  }
  .brand-name {
    display: flex;
    align-items: center;
    gap: 12px;
    font-family: "Montserrat", sans-serif;
    font-weight: 600;
    font-size: 30px;
    letter-spacing: 2px;
    color: var(--text-white);
  }
  .brand-name .dot {
    width: 22px;
    height: 22px;
    border-radius: 50%;
    background: var(--accent-blue);
  }
</style>
</head>
<body>
  <main class="canvas">
    <section class="card card-back" aria-label="Contact side">
      <div class="corner-mark"><span class="dot"></span>CREWWELL CLINICS</div>
      <div class="identity">
        <p class="person-name">Daniel Harper</p>
        <p class="person-title">President</p>
      </div>
      <div class="divider"></div>
      <ul class="contact">
        <li class="address">4120 Harbor View Road</li>
        <li class="address">Kodiak, Alaska 99615</li>
        <li>
          <svg viewBox="0 0 10 10" aria-hidden="true"><path d="M2 1 L4 1 L4.6 3 L3.5 4 Q4.5 6 6 6.5 L7 5.4 L9 6 L9 8 Q5 9 2.5 6 Q0.8 3.5 2 1 Z" fill="var(--accent-blue)"/></svg>
          555-204-7316
        </li>
        <li>
          <svg viewBox="0 0 10 10" aria-hidden="true"><rect x="2.5" y="0.8" width="5" height="8.4" rx="0.8" fill="none" stroke="var(--text-white)" stroke-width="1"/></svg>
          555-318-6042
        </li>
        <li>
          <svg viewBox="0 0 10 10" aria-hidden="true"><rect x="0.5" y="1.5" width="9" height="7" fill="var(--accent-blue)"/><path d="M0.5 1.5 L5 5.5 L9.5 1.5" fill="none" stroke="var(--card-navy)" stroke-width="1"/></svg>
          hello@crewwellclinics.com
        </li>
        <li>
          <svg viewBox="0 0 10 10" aria-hidden="true"><circle cx="5" cy="5" r="4.5" fill="var(--accent-blue)"/><path d="M0.5 5 H9.5 M5 0.5 Q2.5 5 5 9.5 M5 0.5 Q7.5 5 5 9.5" fill="none" stroke="var(--card-navy)" stroke-width="0.7"/></svg>
          crewwellclinics.com
        </li>
      </ul>
    </section>

    <section class="card card-front" aria-label="Brand side">
      <div class="brand-name"><span class="dot"></span>CREWWELL CLINICS</div>
    </section>
  </main>
</body>
</html>
```